Haulage company, lets use ruby red white and some 3rd color for web design. and Garvel Pryce Transport logo

Target Market(s)

Transport industry

Industry/Entity Type

transport

Number of Pages Required

2 page

Requirements
Must have
• Logo

```html
<!DOCTYPE html>
<html lang="en">
<head>
<meta charset="UTF-8">
<title>Garvel Pryce Transport</title>
<link href="https://fonts.googleapis.com/css2?family=Michroma&family=Lato:wght@400;700&display=swap" rel="stylesheet">
<style>
:root{
  --ruby:#a0131f;
  --ruby-dark:#8c0f1a;
  --ink:#111111;
  --white:#ffffff;
  --mist:#f6f6f7;
  --line:#d0d0d4;
  --text:#333333;
}
*{margin:0;padding:0;box-sizing:border-box}
html,body{width:1200px;height:3603px;overflow:hidden}
body{position:relative;background:var(--white);font-family:'Lato',sans-serif;color:var(--text)}
.display{font-family:'Michroma',sans-serif;font-weight:400;-webkit-text-stroke:.5px currentColor;white-space:nowrap}
.abs{position:absolute}
.red{color:var(--ruby)}
.btn{position:absolute;display:flex;align-items:center;justify-content:center;font-family:'Michroma',sans-serif;font-size:10px;letter-spacing:.5px;-webkit-text-stroke:.3px currentColor;white-space:nowrap}
.btn::before{content:"";position:absolute;inset:0;border:2px solid var(--ruby);border-radius:7px;transform:skewX(-14deg)}
.btn.on-dark::before{border-color:var(--white)}
.btn span{position:relative}

/* header */
.site-header{position:absolute;left:0;top:0;width:1200px;height:85px;background:var(--white)}
.brand-name{font-family:'Michroma',sans-serif;font-size:18px;color:var(--ink);letter-spacing:.5px;-webkit-text-stroke:.5px currentColor;white-space:nowrap}
.brand-tag{font-family:'Lato',sans-serif;font-size:11px;letter-spacing:3px;color:var(--ruby)}
.nav a{position:absolute;top:34px;font-family:'Michroma',sans-serif;font-size:11px;color:var(--ink);text-decoration:none;letter-spacing:.3px;-webkit-text-stroke:.3px currentColor;white-space:nowrap}

/* hero */
.hero{position:absolute;left:0;top:85px;width:1200px;height:584px;background:linear-gradient(90deg,#050505 0%,#0e0e10 28%,#3a3a40 55%,#6c6a6f 75%,#4b4a50 100%)}
.hero-text{position:absolute;left:110px;color:var(--white)}

/* stats */
.stat{position:absolute;top:725px;text-align:center;width:340px}
.stat-num{font-family:'Michroma',sans-serif;font-size:20px;color:var(--ruby);letter-spacing:1px;-webkit-text-stroke:.5px currentColor}
.stat-label{margin-top:18px;font-size:18px;color:var(--ruby)}
.stat-divider{position:absolute;top:710px;width:1px;height:105px;background:var(--ruby)}

.photo{position:absolute}
.section-title{position:absolute;font-family:'Michroma',sans-serif;color:var(--ink);letter-spacing:.5px;-webkit-text-stroke:.8px currentColor;white-space:nowrap}
.copy{position:absolute;font-size:15px;line-height:29px;text-align:justify;color:var(--text)}

/* services */
.services{position:absolute;left:0;top:1478px;width:1200px;height:490px;background:var(--mist)}
.card{position:absolute;top:1610px;width:301px;height:238px}
.card .photo{left:0;top:0;width:301px;height:238px}
.card .badge{position:absolute;right:0;top:175px;width:40px;height:38px;background:var(--ruby);display:flex;align-items:center;justify-content:center}
.card-body{position:absolute;top:215px;left:35px;width:275px;background:var(--white);padding:10px 12px 0}
.card-title{font-family:'Michroma',sans-serif;font-size:13px;color:var(--ink);-webkit-text-stroke:.4px currentColor;white-space:nowrap}
.card-text{font-size:11px;line-height:22px;margin-top:4px;color:#444}
.arrow{position:absolute;top:1731px;width:32px;height:32px;border-radius:50%;background:var(--ruby);display:flex;align-items:center;justify-content:center}

/* contact */
.contact{position:absolute;left:0;top:2576px;width:1200px;height:588px;background:var(--mist)}
.field{position:absolute;background:var(--white);border:1px solid var(--line);font-size:15px;font-weight:700;color:#222;padding:28px 0 0 24px}

/* footer */
.site-footer{position:absolute;left:0;top:3164px;width:1200px;height:439px;background:#000;color:var(--white)}
.foot-head{position:absolute;top:78px;font-family:'Michroma',sans-serif;font-size:14px;letter-spacing:.3px;-webkit-text-stroke:.4px currentColor;white-space:nowrap}
.social{position:absolute;top:155px;width:32px;height:32px;border-radius:50%;background:var(--white)}
.c-icon{position:absolute;width:32px;height:32px;border-radius:5px;background:var(--white);display:flex;align-items:center;justify-content:center}
.c-text{position:absolute;font-size:15px;line-height:27px;white-space:nowrap}
.qlink{position:absolute;left:955px;font-size:15px;display:flex;align-items:center;gap:8px}
</style>
</head>
<body>

<header class="site-header">
  <div class="abs" style="left:110px;top:20px">
    <div class="brand-name">GARVEL PRYCE</div>
    <div class="brand-tag" style="margin-top:6px">TRANSPORT</div>
  </div>
  <nav class="nav">
    <a style="left:443px" href="#">HOME</a>
    <a style="left:529px" href="#">SERVICES</a>
    <a style="left:650px" href="#">WHY CHOOSE US</a>
    <a style="left:826px" href="#">SUPPORT</a>
  </nav>
  <div class="btn red" style="left:952px;top:25px;width:132px;height:36px"><span>CONTACT US</span></div>
</header>

<section class="hero" role="img" aria-label="Night photo of white and ruby haulage trucks parked in a yard">
  <div class="hero-text display" style="top:130px;font-size:16px;letter-spacing:.5px">WELCOME TO</div>
  <div class="hero-text display" style="top:168px;font-size:38px;letter-spacing:1px;-webkit-text-stroke:1px currentColor">GARVEL PRYCE</div>
  <div class="hero-text display" style="top:247px;font-size:12px;letter-spacing:5px;color:var(--ruby)">TRANSPORT</div>
  <p class="hero-text" style="top:285px;width:450px;font-size:15px;line-height:29px">Itaque earum rerum hic tenetur a sapiente delectus, ut aut reiciendis voluptatibus maiores alias consequatur aut perferendis doloribus asperiores repellat.</p>
  <div class="btn on-dark" style="left:114px;top:398px;width:136px;height:36px;color:var(--white)"><span>GET STARTED</span></div>
</section>

<section aria-label="Key figures">
  <div class="stat" style="left:45px"><div class="stat-num">120,000,000+</div><div class="stat-label">Temporibus autem quibus</div></div>
  <div class="stat-divider" style="left:426px"></div>
  <div class="stat" style="left:436px"><div class="stat-num">2,000,000</div><div class="stat-label">Itaque earum rerum hic ten</div></div>
  <div class="stat-divider" style="left:766px"></div>
  <div class="stat" style="left:748px"><div class="stat-num">100%</div><div class="stat-label">Sapiente delectus, ut aut</div></div>
</section>

<section aria-label="About">
  <div class="abs" style="left:0;top:883px;width:473px;height:436px;background:var(--ruby)"></div>
  <div class="photo" role="img" aria-label="Ruby and white truck parked on a concrete yard under a pale sky" style="left:110px;top:952px;width:487px;height:437px;background:linear-gradient(180deg,#b9cde0 0%,#c9d6e0 40%,#8c9089 62%,#b7b4ad 100%)"></div>
  <div class="section-title" style="left:662px;top:990px;font-size:26px">ABOUT <span class="red">GARVEL PRYCE</span></div>
  <div class="abs display" style="left:659px;top:1048px;font-size:16px;letter-spacing:5px;color:var(--ruby);-webkit-text-stroke:0">TRANSPORT</div>
  <p class="copy" style="left:666px;top:1086px;width:414px">Nam libero tempore, cum soluta nobis est eligendi optio cumque nihil impedit quo minus id quod maxime placeat facere possimus, omnis voluptas assumenda est, omnis dolor repellendus.</p>
  <p class="copy" style="left:666px;top:1231px;width:414px;text-align:left">Temporibus autem quibusdam et aut officiis debitis aut rerum necessitatibus saepe eveniet ut et voluptates repudiandae sint et molestiae non recusandae.</p>
  <div class="btn red" style="left:673px;top:1334px;width:134px;height:36px"><span>READ MORE</span></div>
</section>

<section class="services" aria-label="Our services"></section>
<div class="section-title" style="left:0;width:1200px;text-align:center;top:1536px;font-size:30px">OUR <span class="red">SERVICES</span></div>
<div class="arrow" style="left:33px"><svg width="14" height="14" viewBox="0 0 14 14"><path d="M9 2 4 7l5 5" fill="none" stroke="#fff" stroke-width="2.2"/></svg></div>
<div class="arrow" style="left:1128px"><svg width="14" height="14" viewBox="0 0 14 14"><path d="M5 2l5 5-5 5" fill="none" stroke="#fff" stroke-width="2.2"/></svg></div>

<article class="card" style="left:112px">
  <div class="photo" role="img" aria-label="Two trucks on a coastal road under a cloudy sky" style="background:linear-gradient(180deg,#7fa4cf 0%,#c7d6e6 38%,#6f7a80 60%,#3c3f42 100%)"></div>
  <div class="badge"><svg width="20" height="20" viewBox="0 0 20 20" fill="none" stroke="#fff" stroke-width="1.6"><rect x="3" y="5" width="14" height="11"/><path d="M3 9h14"/></svg></div>
  <div class="card-body"><div class="card-title">Temporibus autem</div><div class="card-text">Temporibus autem quibusdam et aut officiis debitis aut rerum necessitatibus saepe</div></div>
</article>
<article class="card" style="left:446px">
  <div class="photo" role="img" aria-label="Front of a ruby and white truck parked outdoors" style="background:linear-gradient(180deg,#8fa9c4 0%,#e6e3df 35%,#8e2430 60%,#3a3a3c 100%)"></div>
  <div class="badge"><svg width="20" height="20" viewBox="0 0 20 20" fill="none" stroke="#fff" stroke-width="1.6"><circle cx="10" cy="10" r="7"/><path d="M3 10h14M10 3v14"/></svg></div>
  <div class="card-body"><div class="card-title">Itaque earum rerum</div><div class="card-text">Eveniet ut et voluptates repudiandae sint et moles iae non recusandae</div></div>
</article>
<article class="card" style="left:787px">
  <div class="photo" role="img" aria-label="Truck with trailer parked in a yard" style="background:linear-gradient(180deg,#a9c0d9 0%,#ededea 40%,#96303a 62%,#4a4a4c 100%)"></div>
  <div class="badge"><svg width="20" height="20" viewBox="0 0 20 20" fill="none" stroke="#fff" stroke-width="1.6"><circle cx="10" cy="6" r="3"/><path d="M4 17c0-4 3-6 6-6s6 2 6 6"/></svg></div>
  <div class="card-body"><div class="card-title">Nam libero tempore,</div><div class="card-text">Nerniet ut et voluptates repudiandae sint et moles iae non recusandae</div></div>
</article>

<section aria-label="Why choose us">
  <div class="abs" style="left:727px;top:1986px;width:473px;height:435px;background:var(--ruby)"></div>
  <div class="photo" role="img" aria-label="Ruby and white truck cab parked at dusk" style="left:599px;top:2059px;width:486px;height:435px;background:linear-gradient(180deg,#4c6d9c 0%,#a7a4b4 40%,#8a2a35 65%,#404043 100%)"></div>
  <div class="section-title" style="left:107px;top:2106px;font-size:30px">WHY <span class="red">CHOOSE US</span></div>
  <p class="copy" style="left:111px;top:2156px;width:414px">Nam libero tempore, cum soluta nobis est eligendi optio cumque nihil impedit quo minus id quod maxime placeat facere possimus, omnis voluptas assumenda est, omnis dolor repellendus.</p>
  <p class="copy" style="left:111px;top:2301px;width:414px;text-align:left">Temporibus autem quibusdam et aut officiis debitis aut rerum necessitatibus saepe eveniet ut et voluptates repudiandae sint et molestiae non recusandae.</p>
  <div class="btn red" style="left:116px;top:2404px;width:134px;height:36px"><span>VIEW MORE</span></div>
</section>

<section class="contact" aria-label="Get in touch"></section>
<div class="section-title" style="left:0;width:1200px;text-align:center;top:2621px;font-size:30px">GET IN <span class="red">TOUCH WITH US</span></div>
<div class="field" style="left:112px;top:2688px;width:468px;height:67px">Name</div>
<div class="field" style="left:617px;top:2688px;width:468px;height:67px">Email</div>
<div class="field" style="left:112px;top:2775px;width:468px;height:67px">Phone Number</div>
<div class="field" style="left:617px;top:2775px;width:468px;height:67px">Address</div>
<div class="field" style="left:112px;top:2861px;width:975px;height:160px">Message</div>
<div class="btn red" style="left:536px;top:3070px;width:132px;height:36px"><span>SUBMIT</span></div>

<footer class="site-footer">
  <div class="abs" style="left:111px;top:76px">
    <div class="brand-name" style="color:var(--white);font-size:18px">GARVEL PRYCE</div>
    <div class="brand-tag" style="margin-top:8px;font-size:13px">TRANSPORT</div>
  </div>
  <div class="social" style="left:111px"></div>
  <div class="social" style="left:166px"></div>
  <div class="social" style="left:224px"></div>

  <div class="foot-head" style="left:387px">SUBSCRIBE US</div>
  <p class="abs" style="left:387px;top:111px;width:220px;font-size:12px;line-height:26px">Itaque earum rerum hic tenetur a voluptatibus maiores aliasr</p>
  <div class="abs" style="left:386px;top:163px;width:230px;height:48px;background:var(--white);color:#777;font-size:14px;padding:16px 0 0 18px">Enter The Email</div>
  <div class="abs" style="left:385px;top:229px;width:187px;height:56px;background:var(--ruby);border-radius:6px;font-weight:700;font-size:17px;padding:18px 0 0 20px">Subscribe</div>

  <div class="foot-head" style="left:694px">CONTACT US</div>
  <div class="c-icon" style="left:694px;top:112px"><svg width="16" height="18" viewBox="0 0 16 18"><path d="M8 1a6 6 0 0 0-6 6c0 4.5 6 10 6 10s6-5.5 6-10a6 6 0 0 0-6-6z" fill="#111"/><circle cx="8" cy="7" r="2.2" fill="#fff"/></svg></div>
  <div class="c-text" style="left:738px;top:106px">Garvel Pryce Transport<br>United States</div>
  <div class="c-icon" style="left:694px;top:190px"><svg width="16" height="16" viewBox="0 0 16 16"><path d="M3 1l3 3-2 2c1 2 3 4 5 5l2-2 3 3-2 3C7 15 1 9 1 3z" fill="#111"/></svg></div>
  <div class="c-text" style="left:738px;top:190px">+1 555 014 2290</div>
  <div class="c-icon" style="left:694px;top:260px"><svg width="16" height="12" viewBox="0 0 16 12"><rect width="16" height="12" rx="1" fill="#111"/><path d="M1 1l7 6 7-6" fill="none" stroke="#fff" stroke-width="1.4"/></svg></div>
  <div class="c-text" style="left:738px;top:260px">info@garvelprycehaul.com</div>

  <div class="foot-head" style="left:955px">QUICK LINK</div>
  <div class="qlink" style="top:116px"><svg width="14" height="12" viewBox="0 0 14 12"><path d="M1 6h11M7 1l5 5-5 5" fill="none" stroke="#fff" stroke-width="2"/></svg>Home</div>
  <div class="qlink" style="top:150px"><svg width="14" height="12" viewBox="0 0 14 12"><path d="M1 6h11M7 1l5 5-5 5" fill="none" stroke="#fff" stroke-width="2"/></svg>About</div>
  <div class="qlink" style="top:184px"><svg width="14" height="12" viewBox="0 0 14 12"><path d="M1 6h11M7 1l5 5-5 5" fill="none" stroke="#fff" stroke-width="2"/></svg>Services</div>
  <div class="qlink" style="top:218px"><svg width="14" height="12" viewBox="0 0 14 12"><path d="M1 6h11M7 1l5 5-5 5" fill="none" stroke="#fff" stroke-width="2"/></svg>Why Choose us</div>
  <div class="qlink" style="top:252px"><svg width="14" height="12" viewBox="0 0 14 12"><path d="M1 6h11M7 1l5 5-5 5" fill="none" stroke="#fff" stroke-width="2"/></svg>Contact Us</div>

  <div class="abs" style="left:111px;top:349px;width:978px;height:1px;background:#bbb"></div>
  <div class="abs" style="left:0;top:384px;width:1200px;text-align:center;font-size:15px">Copyrights@2024.Garvel Pryce Transport.All Rights Reserved</div>
</footer>

</body>
</html>
```